TV Antenna Installation business needs a unique flyer

We need a simple but effective flyer design for our TV Aerial installation company based in Newcastle, NSW, Australia called Bright Harbour TV & Aerial Svcs.
We are trying to target areas where there has been a new transmitter installed and most houses just require their aerial redirecting and tv's retuning.

Industry/Entity Type

Business

Requirements
Must have
• We would like the idea of a headline phrase such as " Poor TV reception……..now a thing from the past" or something similar & catchy.
Also "Did you know a new transmitter has been recently installed in your area, we can therefore now GUARANTEE 100% PERFECT PICTURE
Charges from only $95.
- Free 5 year warranty
- Free signal testing
- Free Onsite Quote
Phone 0463 527 209
Nice to have
• Other services include:

- New Installs
- Extra Points & repairs
- TV wall mounting/Home Cinema
- Pull down tall masts

Modern tv picture, see example uploaded

```html
<!DOCTYPE html>
<html lang="en">
<head>
<meta charset="utf-8">
<title>Bright Harbour TV &amp; Aerial Svcs – Flyer</title>
<link rel="stylesheet" href="https://fonts.googleapis.com/css2?family=Montserrat:wght@600;700&family=Questrial&family=Oswald:wght@400;500&family=Roboto+Condensed:wght@700&display=swap">
<style>
  :root {
    --purple: #8a4a9e;
    --lavender: #c3c0e2;
    --orange: #f26b0c;
    --green: #3d8c3f;
    --star: #3f9a4c;
    --ink: #3a3a3a;
    --white: #ffffff;
    --paper: #f7f7f7;
    --tv-mint: #b3e2d2;
    --tv-rust: #8a3b1c;
  }
  * { margin: 0; padding: 0; box-sizing: border-box; }
  html, body { width: 906px; height: 1200px; overflow: hidden; background: var(--paper); }
  .flyer {
    position: relative; width: 906px; height: 1200px; overflow: hidden;
    background: radial-gradient(ellipse at 50% 45%, #ffffff 0%, #f3f3f3 70%, #ebebeb 100%);
    font-family: "Questrial", sans-serif; color: var(--ink);
  }
  .shape { position: absolute; left: 0; top: 0; }
  .title {
    position: absolute; left: 0; top: 13px; width: 906px; height: 74px;
    display: flex; align-items: center; justify-content: center;
    font-family: "Montserrat", sans-serif; font-weight: 600; font-size: 46px;
    color: var(--white); letter-spacing: 0.5px;
  }
  .hero-art {
    position: absolute; border-radius: 14px;
    background: radial-gradient(ellipse at 50% 45%, var(--tv-mint) 0%, #d7c7b4 45%, #c97a4e 75%, var(--tv-rust) 100%);
  }
  .hero-art--before { left: 66px; top: 240px; width: 156px; height: 258px; }
  .hero-art--after { left: 522px; top: 204px; width: 226px; height: 350px; }
  .pitch {
    position: absolute; left: 0; top: 558px; width: 906px; text-align: center;
    font-family: "Montserrat", sans-serif; font-weight: 700; font-size: 32px; line-height: 43px;
    color: var(--ink);
  }
  .pitch__guarantee { color: var(--green); }
  .price {
    position: absolute; left: 25px; top: 702px; height: 72px;
    display: flex; align-items: center; font-size: 36px; color: var(--white);
  }
  .perks, .services { position: absolute; list-style: none; font-size: 24.5px; color: #222; }
  .perks { left: 58px; top: 795px; }
  .perks li { height: 34px; display: flex; align-items: center; gap: 12px; }
  .services { left: 422px; top: 1005px; }
  .services li { height: 35.5px; display: flex; align-items: center; gap: 12px; }
  .star { width: 24px; height: 24px; flex: none; }
  .call {
    position: absolute; left: 470px; top: 734px; width: 420px; height: 155px;
    color: var(--white); text-align: center;
  }
  .call__label { font-family: Arial, Helvetica, sans-serif; font-size: 68px; line-height: 74px; }
  .call__number { font-family: "Roboto Condensed", sans-serif; font-weight: 700; font-size: 72px; line-height: 76px; letter-spacing: 1px; }
  .services-title {
    position: absolute; left: 423px; top: 905px; height: 72px;
    display: flex; align-items: center; font-size: 44px; font-weight: 400; color: var(--white);
  }
  .photo { position: absolute; border: 5px solid var(--white); outline: 4px solid var(--lavender); }
  .photo--wall { left: 22px; top: 907px; width: 248px; height: 167px;
    background: linear-gradient(180deg, #b9ad9c 0%, #8b95ad 45%, #4a4f62 70%, #6b5a48 100%); }
  .photo--lounge { left: 145px; top: 1009px; width: 252px; height: 170px;
    background: linear-gradient(160deg, #e6e8ea 0%, #a9adb2 50%, #6a7682 75%, #c9b89d 100%); }
</style>
</head>
<body>
<main class="flyer">
  <svg class="shape" width="906" height="1200" viewBox="0 0 906 1200" aria-hidden="true">
    <polygon points="9,50 52,13 854,13 891,50 854,87 52,87" fill="var(--lavender)"/>
    <polygon points="22,50 60,17 846,17 878,50 846,83 60,83" fill="var(--purple)"/>
    <polygon points="0,152 255,152 470,343 255,533 0,533" fill="var(--lavender)"/>
    <polygon points="255,152 310,152 470,343 310,533 255,533 418,343" fill="var(--purple)"/>
    <polygon points="0,162 906,111 906,171 0,228" fill="var(--orange)"/>
    <text x="20" y="216" transform="rotate(-3.6 20 216)" font-family="Oswald, sans-serif" font-size="44" fill="#fff" textLength="852" lengthAdjust="spacingAndGlyphs">Poor TV reception........now a thing from the past !</text>
    <polygon points="0,702 395,702 433,738 395,774 0,774" fill="var(--lavender)"/>
    <polygon points="0,702 384,702 420,738 384,774 0,774" fill="var(--purple)"/>
    <polygon points="546,734 906,734 906,889 392,889" fill="var(--orange)"/>
    <polygon points="369,941 405,905 906,905 906,977 405,977" fill="var(--lavender)"/>
    <polygon points="381,941 415,905 906,905 906,977 415,977" fill="var(--purple)"/>
    <defs>
      <symbol id="star" viewBox="0 0 24 24"><polygon points="12,1 15,9 23,9 16.5,14 19,22 12,17 5,22 7.5,14 1,9 9,9" fill="var(--star)"/></symbol>
    </defs>
  </svg>

  <h1 class="title">Bright Harbour TV &amp; Aerial Svcs</h1>

  <div class="hero-art hero-art--before" role="img" aria-label="Cartoon retro TV on legs showing a static signal line"></div>
  <div class="hero-art hero-art--after" role="img" aria-label="Larger cartoon retro TV on legs with a happy screen"></div>

  <p class="pitch">Did you know a new transmitter has been recently<br>installed in your area, we can therefore now<br><span class="pitch__guarantee">GUARANTEE 100% PERFECT PICTURE</span> !</p>

  <p class="price">Charges from only $95</p>

  <ul class="perks">
    <li><svg class="star"><use href="#star"/></svg>Free 5 year warranty</li>
    <li><svg class="star"><use href="#star"/></svg>Free signal testing</li>
    <li><svg class="star"><use href="#star"/></svg>Free Onsite Quote</li>
  </ul>

  <div class="call">
    <p class="call__label">Call Now</p>
    <p class="call__number">0463 527 209</p>
  </div>

  <h2 class="services-title">Other services include</h2>

  <ul class="services">
    <li><svg class="star"><use href="#star"/></svg>New Installs</li>
    <li><svg class="star"><use href="#star"/></svg>Extra Outlets &amp; repairs</li>
    <li><svg class="star"><use href="#star"/></svg>TV wall mounting / Home Cinema</li>
    <li><svg class="star"><use href="#star"/></svg>Pull down tall masts</li>
  </ul>

  <div class="photo photo--wall" role="img" aria-label="Photo of a flat-screen TV mounted on a living room wall"></div>
  <div class="photo photo--lounge" role="img" aria-label="Photo of a modern lounge with a large TV on a stand"></div>
</main>
</body>
</html>
```